Custom Manufacturing Company square space website design

I own a custom manufacturing company that uses precision cutting technology to manufacture project components over a couple industries. We have an industrial CNC router and state of the art edge bander and cut a lot of cabinetry components for cabinet shops, builders, closet companies, ect. We offer design and assembly for any cabinetry or can build cabinets to spec. We also cut components for other industries out of wood, plastics, acryclics, ect. We offer design engineering services, product development protype services. we have a 3D printer farm. We want our communicate trust, dependability, and the value we place on client relationships.

We essentially want a credibility website. Landing page and drops downs for services we offer, capabilites, about us, contact

```html
<!DOCTYPE html>
<html lang="en">
<head>
<meta charset="utf-8">
<title>North Loop Fabrication</title>
<link rel="stylesheet" href="https://fonts.googleapis.com/css2?family=Michroma&family=Inter:wght@400;500&family=Libre+Baskerville&display=swap">
<style>
:root{
  --ink:#0d0f0f;
  --dark:#121414;
  --black:#000000;
  --white:#ffffff;
  --orange:#ff6a00;
  --muted:#c9c9c9;
  --line:#d7d7d7;
  --wood-1:#c99a6c;
  --wood-2:#8a5a34;
  --wood-3:#e9dccd;
}
*{box-sizing:border-box;margin:0;padding:0}
html,body{width:1200px;height:3757px;overflow:hidden}
body{position:relative;background:var(--white);font-family:"Inter",Arial,sans-serif;color:var(--ink)}
.display{font-family:"Michroma",sans-serif;font-weight:400}
.abs{position:absolute}
.btn{position:absolute;background:var(--orange);color:var(--ink);font-family:"Michroma",sans-serif;font-size:18px;display:flex;align-items:center;justify-content:center;clip-path:polygon(0 0,100% 0,100% 100%,14px 100%,0 calc(100% - 14px))}
.rule{position:absolute;height:3px;border-radius:2px}

/* hero */
.hero{position:absolute;left:0;top:0;width:1200px;height:618px;background:linear-gradient(100deg,var(--wood-3) 0%,#d8c2a6 30%,var(--wood-1) 60%,var(--wood-2) 100%)}
.brand{position:absolute;left:98px;top:30px;display:flex;align-items:center;gap:12px}
.brand-square{width:22px;height:22px;border:2px solid var(--ink)}
.brand-name{font-family:"Michroma",sans-serif;font-size:16px;letter-spacing:2px}
.nav{position:absolute;top:36px;font-family:"Michroma",sans-serif;font-size:18px}
.hero-card{position:absolute;left:79px;top:182px;width:474px;height:282px;background:var(--white)}
.hero-card .welcome{position:absolute;left:19px;top:20px;font-size:28px}
.hero-card .title{position:absolute;left:19px;top:70px;font-size:41px;white-space:nowrap}
.hero-card p{position:absolute;left:19px;top:138px;width:420px;font-size:11.5px;line-height:21px;color:#444}

/* about */
.about{position:absolute;left:0;top:618px;width:1200px;height:642px;background:var(--dark)}
.section-title{font-size:34px;color:var(--white)}
.body-copy{font-size:15.5px;line-height:29px;color:#e8e8e8}

/* services */
.services{position:absolute;left:0;top:1260px;width:1200px;height:889px;background:linear-gradient(180deg,#ffffff 0%,#f4f5f7 45%,#e1e4e6 80%,#d7d9d6 100%)}
.card{position:absolute;top:199px;width:488px;height:423px;background:var(--black);clip-path:polygon(0 0,100% 0,100% calc(100% - 66px),calc(100% - 66px) 100%,0 100%)}
.card .photo{position:absolute;left:13px;top:12px;width:462px;height:255px;border-radius:6px}
.card p{position:absolute;left:20px;top:284px;width:440px;font-family:"Michroma",sans-serif;font-size:13.5px;line-height:26px;color:var(--white);letter-spacing:-.5px;text-transform:uppercase}

/* capabilities */
.capabilities{position:absolute;left:0;top:2149px;width:1200px;height:672px;background:linear-gradient(90deg,#6b4a35 0%,#b08966 35%,#cdb08e 70%,#d8c1a2 100%)}

/* contact */
.label{position:absolute;font-family:"Michroma",sans-serif;font-size:13px;color:#333}
.field{position:absolute;border:2px solid var(--line);border-radius:14px;background:var(--white)}

/* footer */
.footer{position:absolute;left:0;top:3482px;width:1200px;height:275px;background:var(--dark);color:var(--white)}
.footer .nav{top:61px;color:var(--white)}
.social{position:absolute;top:97px;width:41px;height:41px;border-radius:50%;background:var(--white)}
</style>
</head>
<body>

<header class="hero" role="img" aria-label="Photo of a modern staircase with built-in walnut cabinetry and drawers">
  <div class="brand">
    <span class="brand-square"></span>
    <span class="brand-name">NORTH LOOP</span>
  </div>
  <span class="nav" style="left:344px">Home</span>
  <span class="nav" style="left:453px">Services We Offer</span>
  <span class="nav" style="left:691px">Capabilities</span>
  <span class="nav" style="left:856px">About Us</span>
  <span class="nav" style="left:1000px">Contact</span>

  <div class="hero-card">
    <h2 class="display welcome">Welcome to</h2>
    <h1 class="display title" style="font-size:35px">North Loop Fab</h1>
    <p>Lorem ipsum dolor sit amet, consectetur adipiscing elit, sed do eiusmod tempor incididunt ut labore et dolore magna aliqua.</p>
    <a class="btn" style="left:19px;top:203px;width:176px;height:54px">Get Started</a>
  </div>
</header>

<section class="about">
  <svg class="abs" style="left:82px;top:72px" width="440" height="484" viewBox="0 0 440 484">
    <polyline points="2,14 2,481 256,481 275,462" fill="none" stroke="#ffffff" stroke-width="3"/>
  </svg>
  <div class="abs" role="img" aria-label="Photo of a white walk-in closet with shelves, hanging rods and drawers"
       style="left:98px;top:72px;width:420px;height:469px;background:linear-gradient(135deg,#f4f4f4 0%,#dcdcdc 55%,#8e8e8e 100%);clip-path:polygon(0 0,100% 0,100% 82%,82% 100%,0 100%)"></div>

  <h2 class="display section-title abs" style="left:599px;top:100px">ABOUT US</h2>
  <span class="rule" style="left:599px;top:145px;width:126px;background:linear-gradient(90deg,#fff,#555)"></span>
  <p class="body-copy abs" style="left:599px;top:164px;width:505px">Sed ut perspiciatis unde omnis iste natus error sit voluptatem accusantium doloremque laudantium, totam rem aperiam, eaque ipsa quae ab illo inventore veritatis et quasi architecto beatae vitae dicta sunt explicabo. Nemo enim ipsam voluptatem quia voluptas sit aspernatur aut odit aut fugit, sed quia consequuntur magni dolores eos qui ratione voluptatem sequi nesciunt. Neque porro quisquam est, qui dolorem ipsum quia dolor sit amet, consectetur, adipisci velit, sed quia non numquam eius modi tempora incidunt ut labore et dolore magnam aliquam quaerat voluptatem.</p>
  <a class="btn" style="left:604px;top:458px;width:194px;height:51px">Read More</a>
</section>

<section class="services">
  <div class="abs" role="img" aria-label="Faded photo of an industrial manufacturing building"
       style="left:0;top:560px;width:1200px;height:329px;background:linear-gradient(180deg,rgba(225,228,230,0) 0%,rgba(190,194,192,.45) 100%)"></div>
  <h2 class="display abs" style="left:0;width:1200px;text-align:center;top:106px;font-size:34px">SERVICES WE OFFER</h2>
  <span class="rule" style="left:536px;top:156px;width:127px;background:linear-gradient(90deg,#111,#888)"></span>

  <article class="card" style="left:98px">
    <div class="photo" role="img" aria-label="Photo of a smiling craftsman working at a manufacturing bench" style="background:linear-gradient(135deg,#2a2622 0%,#6b5140 50%,#c0642a 100%)"></div>
    <p>We own a custom manufacturing company that uses precision cutting technology to manufacture project components over a couple industries</p>
  </article>
  <article class="card" style="left:612px">
    <div class="photo" role="img" aria-label="Photo of a woodworker assembling cabinet components in a workshop" style="background:linear-gradient(120deg,#7a4e33 0%,#b58862 50%,#d9cfc4 100%)"></div>
    <p>We have an industrial CNC router and state of the art edge bander and cut a lot of cabinetry components for cabinet shops, builders, closet companies, ect.</p>
  </article>

  <a class="btn" style="left:475px;top:682px;width:250px;height:51px">View All Services</a>
</section>

<section class="capabilities" role="img" aria-label="Photo of a carpenter installing plywood cabinet shelving">
  <svg class="abs" style="left:690px;top:86px" width="412" height="520" viewBox="0 0 412 520">
    <polyline points="390,2 409,2 409,517 15,517 0,502" fill="none" stroke="#ffffff" stroke-width="3"/>
  </svg>
  <div class="abs" style="left:513px;top:70px;width:567px;height:515px;background:var(--black);clip-path:polygon(0 0,100% 0,100% 100%,82px 100%,0 calc(100% - 82px))">
    <h2 class="display section-title abs" style="left:45px;top:36px">CAPABILITIES</h2>
    <span class="rule" style="left:45px;top:85px;width:126px;background:linear-gradient(90deg,#fff,#555)"></span>
    <p class="body-copy abs" style="left:45px;top:104px;width:505px">Sed ut perspiciatis unde omnis iste natus error sit voluptatem accusantium doloremque laudantium, totam rem aperiam, eaque ipsa quae ab illo inventore veritatis et quasi architecto beatae vitae dicta sunt explicabo. Nemo enim ipsam voluptatem quia voluptas sit aspernatur aut odit aut fugit, sed quia consequuntur magni dolores eos qui ratione voluptatem sequi nesciunt. Neque porro quisquam est, qui dolorem ipsum quia dolor sit amet, consectetur, adipisci velit, sed quia non numquam eius modi tempora incidunt ut labore et dolore magnam aliquam quaerat voluptatem.</p>
    <a class="btn" style="left:50px;top:400px;width:194px;height:51px">Read More</a>
  </div>
</section>

<section class="contact">
  <h2 class="display abs" style="left:98px;top:2946px;font-size:34px">CONTACT US</h2>
  <span class="rule" style="left:102px;top:3002px;width:124px;background:linear-gradient(90deg,#111,#888)"></span>

  <span class="label" style="left:98px;top:3058px">Name *</span>
  <div class="field" style="left:98px;top:3087px;width:488px;height:61px"></div>
  <span class="label" style="left:98px;top:3178px">Email address *</span>
  <div class="field" style="left:98px;top:3206px;width:488px;height:61px"></div>
  <span class="label" style="left:98px;top:3293px">Phone number *</span>
  <div class="field" style="left:98px;top:3321px;width:488px;height:60px"></div>

  <span class="label" style="left:622px;top:3055px">Message *</span>
  <div class="field" style="left:622px;top:3085px;width:478px;height:159px"></div>
  <div class="abs" style="left:624px;top:3266px;width:29px;height:27px;border:2px solid var(--line);border-radius:7px"></div>
  <p class="abs" style="left:672px;top:3264px;width:400px;font-family:'Libre Baskerville',serif;font-size:13.5px;line-height:23px;color:#333">I allow this website to store my submission so they can respond to my inquiry. *</p>
  <a class="btn" style="left:631px;top:3326px;width:194px;height:49px">Send Now</a>
</section>

<footer class="footer">
  <div class="abs" style="left:99px;top:78px;display:flex;align-items:center;gap:12px">
    <span style="width:26px;height:26px;border:2px solid #fff"></span>
    <span class="display" style="font-size:18px;letter-spacing:2px">NORTH LOOP</span>
  </div>
  <span class="nav" style="left:357px">Home</span>
  <span class="nav" style="left:467px">Services We Offer</span>
  <span class="nav" style="left:704px">Capabilities</span>
  <span class="nav" style="left:869px">About Us</span>
  <span class="nav" style="left:1013px">Contact</span>
  <span class="social" style="left:950px" aria-label="Social profile"></span>
  <span class="social" style="left:1003px" aria-label="Social profile"></span>
  <span class="social" style="left:1056px" aria-label="Social profile"></span>
  <p class="abs" style="right:100px;top:168px;font-size:15px;letter-spacing:-.2px">© copyrights 2023 North Loop Fabrication | All Rights Reserved</p>
</footer>

</body>
</html>
```